GearHive.com

Our company, GearHive Inc., is an established business with an extensive worldwide customer base in the Aviation, Aerospace, and Defense Industries.
GearHive Inc, is an e-commerce platform driven by an aviation parts locator. We are looking to totally redo our homepage, log-in page, standard part search page, and results page.
Our current web design is in 800frame and we need it to be updated to a centered 1280 frame. The new design also needs to be easily viewed from any mobile device. The new size needs to accommodate 2-3 advertisements, both vertically and horizontally.
I like clean, simple, crisp lines that can easily be navigated by everyone. Along with Aviation/Aerospace stock photos, I would like to use different shades of blue and grey and accent specific buttons/drop-downs with orange or yellow.
We are also looking for a web designer who also has the ability to cut up the page and turn over to our .NET developers.
Attached are the 4 pages that I would like to start working on. The standard content within these pages need to be incorporated into the new design.
Our current website is www.gearhive.com
Below are some industry websites that I like the color and feel of.
Please use attached pic of corvane T410 as main photo
http://www.stravelcorp.com/
http://www.quillanor.com/en/aerospace.html
http://www.dexavend.com/
http://aerospace.veltrimax.com/

```html
<!DOCTYPE html>
<html lang="en">
<head>
<meta charset="utf-8">
<title>GearHive.com – Find Stock</title>
<link href="https://fonts.googleapis.com/css2?family=Open+Sans:wght@400;600;700;800&display=swap" rel="stylesheet">
<style>
:root{
  --navy:#0f0f6c;
  --navy-line:#1d1d80;
  --blue:#0f7fd0;
  --blue-dark:#0a62b0;
  --orange:#f0820f;
  --red:#dd1111;
  --yellow:#f4cf4a;
  --panel:#e1ebf3;
  --panel-border:#b9c9d6;
  --tab:#d3e0ea;
  --text:#333;
  --link:#1a7fd6;
  --white:#fff;
}
*{box-sizing:border-box;margin:0;padding:0}
html,body{width:1200px;height:1048px;overflow:hidden}
body{font-family:"Open Sans",sans-serif;color:var(--text);background:var(--white);position:relative}
.abs{position:absolute}
.header{left:0;top:0;width:1200px;height:118px;background:linear-gradient(#fff,#e2e2e2);border-bottom:4px solid var(--navy)}
.brand{left:30px;top:36px;font-size:40px;font-weight:800;color:#1668c8;letter-spacing:-1px}
.ad-slot{left:708px;top:33px;width:460px;height:60px;border:1px solid #d4d4d4;background:#f7f7f7}
.ad-name{left:10px;top:18px;font-size:15px;font-weight:700;color:#1668c8}
.ad-art{left:170px;top:8px;width:280px;height:42px;background:linear-gradient(90deg,#f6dc7a,#f0a04a)}
.sidebar{left:0;top:118px;width:250px;height:930px;background:var(--navy);color:#fff}
.side-link{position:absolute;left:32px;font-size:13.5px;font-weight:600}
.sep{position:absolute;left:0;width:250px;height:1px;background:var(--navy-line)}
.icon-link{position:absolute;left:38px;font-size:13.5px;font-weight:600;display:flex;align-items:center;gap:5px}
.side-btn{position:absolute;left:30px;height:37px;color:#fff;font-size:13.5px;font-weight:600;display:flex;align-items:center;justify-content:center;gap:7px}
.btn-logout{background:var(--red);width:140px}
.btn-overhaul{background:var(--orange);width:152px}
.btn-board{background:var(--blue);width:194px}
.group-title{position:absolute;left:30px;font-size:13.5px;font-weight:600}
.sub-link{position:absolute;left:36px;font-size:13px}
.sub-link::before{content:"→";color:var(--orange);font-weight:700;margin-right:2px}
.cta{top:158px;height:58px;color:#fff;font-size:17px;font-weight:600;display:flex;align-items:center;justify-content:center;gap:14px;border-radius:2px}
.cta-inventory{left:292px;width:265px;background:linear-gradient(#1d8ee0,#0a63b4);box-shadow:0 2px 0 #0a4f90}
.cta-overhaul{left:582px;width:327px;background:linear-gradient(#f6911c,#e07208);box-shadow:0 2px 0 #b85a05}
.search-panel{left:295px;top:243px;width:682px;height:510px;background:var(--panel);border:1px solid var(--panel-border)}
.tabs{display:flex;height:65px;background:var(--tab)}
.tab{display:flex;align-items:center;justify-content:center;font-size:15px;color:#444;border-right:1px solid #b9c9d6}
.tab.active{background:var(--blue);color:#fff;position:relative}
.tab.active::after{content:"";position:absolute;bottom:-9px;left:67px;border:9px solid transparent;border-top-color:var(--blue);border-bottom:0}
.radio{display:inline-block;width:13px;height:13px;border:1px solid #aaa;border-radius:50%;background:#fff;vertical-align:-2px;margin-right:4px}
.radio.on{background:radial-gradient(#555 32%,#fff 38%)}
.row{position:absolute;font-size:14px;white-space:nowrap}
.xref{color:var(--red);margin-right:24px}
.opt{margin-right:14px}
.opt.link{color:var(--link)}
.textarea{left:63px;top:176px;width:556px;height:160px;background:#fff;border:1px solid #c6d2dc}
.select{left:63px;top:349px;width:556px;height:36px;background:linear-gradient(#fff,#f0f0f0);border:1px solid #c6d2dc;font-size:12.5px;padding:9px 14px}
.select::after{content:"";position:absolute;right:14px;top:15px;border:5px solid transparent;border-top-color:#444;border-bottom:0}
.check{left:63px;top:409px;font-size:13.5px;color:#555}
.box{display:inline-block;width:13px;height:13px;border:1px solid #aaa;background:#fff;vertical-align:-2px;margin-right:6px}
.search-btn{left:485px;top:435px;width:134px;height:43px;background:linear-gradient(#1d8ee0,#0a63b4);border-radius:3px;color:#fff;font-size:17px;display:flex;align-items:center;justify-content:center;gap:10px;box-shadow:0 2px 0 #0a4f90}
.updates{left:984px;top:353px;width:202px;height:215px;background:var(--panel);border:1px solid var(--panel-border)}
.updates-title{left:12px;top:9px;font-size:16.5px;color:var(--link);display:flex;align-items:center;gap:8px}
.update-card{left:7px;top:35px;width:186px;height:171px;background:#fff;border:1px solid #c6d2dc}
.update-head{left:10px;top:10px;font-size:14px;color:#222;display:flex;align-items:center;gap:8px}
.update-thumb{width:20px;height:18px;background:linear-gradient(#f3e08a,#d7b33a)}
.update-body{left:7px;top:44px;width:176px;font-size:12.3px;line-height:20px;color:#555}
</style>
</head>
<body>
<header class="header abs">
  <div class="brand abs">GearHive</div>
  <div class="ad-slot abs">
    <div class="ad-name abs">Norvex Trading</div>
    <div class="ad-art abs" role="img" aria-label="Advertiser banner artwork for Norvex Trading"></div>
  </div>
</header>

<nav class="sidebar abs">
  <div class="side-link" style="top:13px">Parts Direct</div>
  <div class="sep" style="top:42px"></div>
  <div class="side-link" style="top:57px">Aerpages</div>
  <div class="sep" style="top:87px"></div>
  <div class="side-link" style="top:101px">Advertisments</div>
  <div class="sep" style="top:133px"></div>
  <div class="icon-link" style="top:151px"><svg width="14" height="13"><rect x="1" y="2" width="10" height="10" fill="none" stroke="#fff" stroke-width="1.5"/><path d="M6 8 L13 1" stroke="#fff" stroke-width="1.5"/></svg>My Profile</div>
  <div class="icon-link" style="top:187px"><svg width="14" height="13"><path d="M1 2h12M1 6h12M1 10h12" stroke="#fff" stroke-width="2"/></svg>Cariobad</div>
  <div class="icon-link" style="top:223px"><svg width="14" height="14"><path d="M1 9 L12 1 L10 13 L7 9 Z" fill="#fff"/></svg>Preferences</div>
  <div class="sep" style="top:262px"></div>
  <div class="side-btn btn-logout" style="top:277px"><svg width="12" height="14"><rect x="1" y="6" width="10" height="7" fill="none" stroke="#fff" stroke-width="1.4"/><path d="M3 6V4a3 3 0 0 1 6 0v2" fill="none" stroke="#fff" stroke-width="1.4"/></svg>Log-Out</div>
  <div class="side-btn btn-overhaul" style="top:327px"><svg width="14" height="14"><circle cx="7" cy="7" r="6" fill="none" stroke="#fff" stroke-width="1.3"/><path d="M1 7h12M7 1v12" stroke="#fff" stroke-width="1"/></svg>Overhaul</div>
  <div class="side-btn btn-board" style="top:377px"><svg width="18" height="14"><rect x="1" y="3" width="14" height="10" fill="none" stroke="#fff" stroke-width="1.5"/><path d="M7 9 L17 1" stroke="#fff" stroke-width="1.5"/></svg>Message Board</div>
  <div class="sep" style="top:432px"></div>
  <div class="group-title" style="top:450px">Buyers</div>
  <div class="sub-link" style="top:479px">Search</div>
  <div class="sub-link" style="top:503px">Batch Search</div>
  <div class="sub-link" style="top:527px">Govt Data</div>
  <div class="sub-link" style="top:551px">List P2Find</div>
  <div class="sub-link" style="top:575px">RFQs</div>
  <div class="sub-link" style="top:599px">RFQs History</div>
  <div class="sub-link" style="top:623px">Pending RFQs</div>
  <div class="sep" style="top:655px"></div>
  <div class="group-title" style="top:670px">Sellers</div>
  <div class="sub-link" style="top:699px">List</div>
  <div class="sub-link" style="top:723px">Parts2Find</div>
  <div class="sub-link" style="top:747px">Quote Hist</div>
  <div class="sub-link" style="top:771px">My Top Slot</div>
  <div class="sep" style="top:804px"></div>
  <div class="icon-link" style="top:820px;left:30px"><svg width="17" height="14"><circle cx="5" cy="4" r="2.5" fill="#fff"/><circle cx="12" cy="4" r="2.5" fill="#fff"/><path d="M0 13a5 5 0 0 1 10 0zM7 13a5 5 0 0 1 10 0z" fill="#fff"/></svg>Our Members</div>
  <div class="sep" style="top:854px"></div>
</nav>

<div class="cta cta-inventory abs">Submit Inventory <svg width="22" height="22"><circle cx="11" cy="11" r="9.5" fill="none" stroke="#fff" stroke-width="2"/><path d="M6 11h9M11 7l4 4-4 4" fill="none" stroke="#fff" stroke-width="2"/></svg></div>
<div class="cta cta-overhaul abs">Submit Overhaul Capabillities <svg width="22" height="22"><circle cx="11" cy="11" r="9.5" fill="none" stroke="#fff" stroke-width="2"/><path d="M6 11h9M11 7l4 4-4 4" fill="none" stroke="#fff" stroke-width="2"/></svg></div>

<section class="search-panel abs">
  <div class="tabs">
    <div class="tab active" style="width:142px">Find Stock</div>
    <div class="tab" style="width:167px">Find Govt Data</div>
    <div class="tab" style="width:164px">Find Messages</div>
    <div class="tab" style="width:207px;border-right:0">Find Who Repairs</div>
  </div>
  <div class="row" style="left:38px;top:87px">By <span class="radio on" style="margin-left:4px"></span>Part Number</div>
  <div class="row" style="left:59px;top:116px;font-size:13.5px"><span class="xref">Cross Reference</span><span class="radio on"></span><span class="opt">None</span><span class="radio"></span><span class="opt link">US MCRL</span><span class="radio"></span><span class="opt link">NATO MCRL</span><span class="radio"></span><span class="opt link">FAA PMA</span></div>
  <div class="row" style="left:62px;top:145px;font-size:13.5px"><span class="radio"></span>Description</div>
  <div class="textarea abs"></div>
  <div class="select abs">Include All Countries</div>
  <div class="check abs"><span class="box"></span>Show results of All Parts in one tab</div>
  <div class="search-btn abs"><svg width="17" height="17"><circle cx="7" cy="7" r="5.5" fill="none" stroke="#fff" stroke-width="2"/><path d="M11 11l5 5" stroke="#fff" stroke-width="2"/></svg>Search</div>
</section>

<aside class="updates abs">
  <div class="updates-title abs"><svg width="16" height="14"><path d="M1 1l7 6 7-6M1 7l7 6 7-6" fill="none" stroke="#1a7fd6" stroke-width="2"/></svg>Important Updates</div>
  <div class="update-card abs">
    <div class="update-head abs"><span class="update-thumb" role="img" aria-label="Certificate icon"></span>Got the Right Part?</div>
    <p class="update-body abs">Lorem ipsum dolor sit amet, consectetuer adipiscing elit, sed diam nonummy nibh euismod tincidunt ut laoreet dolore magna aliquam erat volutpat.</p>
  </div>
</aside>
</body>
</html>
```